Business Card for premium dental clinic

We are a premium dental clinic based in Brasov, Romania with more than 15 year on the market, providing quality dental treatment made by a team of more specialized dentists, working with modern equipment as a solution to beautiful and healthy teeth.

Our current logo for the clinic use 2 square with colors black and gold - dr Ternisu - studio, using family fonts Bodoni, Myriad Pro and Segoe Print.
Depending on the printing we used some gold CMYK background or gold foil picture background or a gold gradient.
We want a business card:
- eye catching business card
- distinguished business card
- premium design
- to keep the color scheme of black and gold
- to attract the customers to spent time reading the information
- modern concept

```html
<!DOCTYPE html>
<html lang="en">
<head>
<meta charset="utf-8">
<title>Dr. Ternisu Studio – Business Card</title>
<link rel="stylesheet" href="https://fonts.googleapis.com/css2?family=Source+Sans+3:wght@400;600&display=swap">
<style>
  :root {
    --backdrop: #c9cacc;
    --card-black: #0b0b0b;
    --gold-deep: #b8860b;
    --gold-mid: #e2b93b;
    --gold-light: #f7e08a;
    --bronze: #9a6a2e;
    --white: #ffffff;
    --ink: #0a0a0a;
  }
  * { box-sizing: border-box; margin: 0; padding: 0; }
  html, body { width: 1200px; height: 800px; overflow: hidden; }
  body {
    background: var(--backdrop);
    font-family: "Source Sans 3", "Myriad Pro", sans-serif;
    position: relative;
  }
  .card {
    position: absolute;
    width: 600px;
    height: 343px;
    background: var(--card-black);
    box-shadow: 0 10px 24px rgba(0,0,0,0.25);
    overflow: hidden;
  }
  .card--front { left: 470px; top: 50px; }
  .card--back  { left: 130px; top: 420px; }

  /* Front */
  .logo-frame {
    position: absolute;
    left: 150px; top: 80px;
    width: 300px; height: 170px;
    padding: 8px;
    background: linear-gradient(90deg, var(--gold-light), var(--gold-mid) 45%, var(--bronze));
    display: flex;
  }
  .logo-foil {
    width: 50%;
    background: linear-gradient(135deg, var(--gold-deep), var(--gold-light) 40%, var(--gold-mid) 70%, var(--gold-deep));
  }
  .logo-panel {
    width: 50%;
    background: var(--card-black);
    position: relative;
    padding: 22px 10px 0 12px;
  }
  .brand-name {
    display: flex; align-items: flex-start; gap: 7px;
    color: var(--gold-light);
    font-size: 23px; font-weight: 400;
    line-height: 1.1;
  }
  .brand-mark { width: 9px; height: 9px; margin-top: 8px; background: var(--gold-light); flex: none; }
  .tagline {
    position: absolute;
    right: 10px; bottom: 8px;
    color: var(--white);
    font-size: 15px; font-weight: 600;
  }

  /* Back */
  .name-plate {
    position: absolute;
    left: 165px; top: 0;
    width: 300px; height: 190px;
    border: 5px solid var(--white);
    border-top: none;
    background: linear-gradient(160deg, var(--gold-mid), var(--gold-light) 35%, var(--gold-deep) 65%, var(--gold-light));
    display: flex; align-items: center; justify-content: center;
  }
  .name-plate__title {
    color: var(--ink);
    font-size: 32px; font-weight: 400;
  }
  .contact {
    position: absolute;
    color: var(--white);
    font-size: 15px; line-height: 1.35;
  }
  .contact__row { display: flex; align-items: center; gap: 8px; }
  .contact__row svg { width: 14px; height: 14px; flex: none; }
  .contact--phones { left: 60px; top: 218px; }
  .contact--online { left: 330px; top: 250px; }
  .contact--address { left: 55px; top: 296px; }
</style>
</head>
<body>

<section class="card card--front" aria-label="Card front">
  <div class="logo-frame">
    <div class="logo-foil" role="img" aria-label="Gold foil texture"></div>
    <div class="logo-panel">
      <p class="brand-name"><span class="brand-mark"></span><span>dr Ternisu<br>studio</span></p>
      <p class="tagline">dental clinic</p>
    </div>
  </div>
</section>

<section class="card card--back" aria-label="Card back">
  <div class="name-plate">
    <h1 class="name-plate__title">Dr. Ternisu Studio</h1>
  </div>

  <div class="contact contact--phones">
    <p class="contact__row">
      <svg viewBox="0 0 14 14" fill="none" stroke="var(--gold-mid)" stroke-width="1.4"><rect x="3.5" y="1" width="7" height="12" rx="1"/><line x1="6" y1="11" x2="8" y2="11"/></svg>
      +40 700 555 018
    </p>
    <p class="contact__row">
      <svg viewBox="0 0 14 14" fill="var(--gold-mid)"><path d="M3 1l2.5 3-1.3 1.5c.8 1.8 2.3 3.3 4.1 4.1L9.8 8.3 13 10.8 11.5 13C6 13 1 8 1 2.5z"/></svg>
      +40 200 555 042
    </p>
  </div>

  <div class="contact contact--online">
    <p class="contact__row">
      <svg viewBox="0 0 14 14" fill="none" stroke="var(--gold-mid)" stroke-width="1.4"><rect x="1" y="3" width="12" height="8"/><path d="M1 3l6 5 6-5"/></svg>
      info@drternisu.ro
    </p>
    <p class="contact__row">
      <svg viewBox="0 0 14 14" fill="none" stroke="var(--gold-mid)" stroke-width="1.2"><circle cx="7" cy="7" r="6"/><ellipse cx="7" cy="7" rx="2.6" ry="6"/><line x1="1" y1="7" x2="13" y2="7"/></svg>
      www.drternisu.ro
    </p>
  </div>

  <p class="contact contact--address">strada Livezii nr 7, Brasov, Romania 500000</p>
</section>

</body>
</html>
```